Marwick Law Letterhead

We need a new letterhead design for a Law Firm. The address for the law firm is 1475 Calloway Street, Suite 210, Houston, Texas 77041. Phone Number: 832-361-9027; Fax Number: 832-614-7359. The logo is uploaded to the project.

```html
<!DOCTYPE html>
<html lang="en">
<head>
<meta charset="utf-8">
<title>Marwick Law Letterhead</title>
<link rel="stylesheet" href="https://fonts.googleapis.com/css2?family=Arimo:wght@400;700&family=Libre+Baskerville:wght@400;700&display=swap">
<style>
  :root {
    --navy: #172b5a;
    --crimson: #8e1520;
    --paper: #ffffff;
    --ink: #1a1a1a;
    --backdrop: #e9e6e1;
    --signature-fill: #eceef2;
  }
  html, body {
    margin: 0;
    padding: 0;
    width: 1200px;
    height: 900px;
    overflow: hidden;
    background: var(--backdrop);
  }
  .letterhead {
    position: absolute;
    left: 266px;
    top: 20px;
    width: 667px;
    height: 860px;
    background: var(--paper);
    box-shadow: 0 2px 10px rgba(0,0,0,0.18);
    overflow: hidden;
    font-family: "Arimo", Arial, sans-serif;
    color: var(--ink);
  }
  .header-band {
    position: absolute;
    left: 0;
    top: 0;
    width: 667px;
    height: 183px;
    display: block;
  }
  .contact {
    position: absolute;
    right: 23px;
    top: 22px;
    text-align: right;
    font-family: "Libre Baskerville", Georgia, serif;
    font-weight: 700;
    font-size: 8.6px;
    letter-spacing: 0.6px;
    color: var(--paper);
    line-height: 13px;
  }
  .contact p { margin: 0; }
  .contact .phone { margin-top: 5px; }
  .contact .fax { margin-top: 4px; }
  .brand {
    position: absolute;
    left: 70px;
    top: 96px;
    display: flex;
    align-items: center;
    gap: 12px;
  }
  .brand-square {
    width: 40px;
    height: 40px;
    background: var(--navy);
  }
  .brand-name {
    font-family: "Libre Baskerville", Georgia, serif;
    font-weight: 400;
    font-size: 26px;
    color: var(--navy);
    letter-spacing: 0.5px;
  }
  .letter-body {
    position: absolute;
    left: 70px;
    right: 68px;
    top: 0;
    font-size: 13.3px;
    line-height: 20.5px;
  }
  .letter-body p { margin: 0; }
  .date { position: absolute; top: 177px; left: 0; }
  .recipient { position: absolute; top: 230px; left: 0; }
  .recipient .name { font-weight: 700; font-size: 14.5px; }
  .content { position: absolute; top: 354px; left: 0; right: 0; text-align: justify; }
  .content .gap { margin-top: 20.5px; }
  .signature {
    position: absolute;
    top: 681px;
    left: 0;
    width: 86px;
    height: 22px;
    background: var(--signature-fill);
  }
  .signer {
    position: absolute;
    top: 710px;
    left: 0;
    font-weight: 700;
    font-size: 15px;
  }
</style>
</head>
<body>
  <main class="letterhead">
    <svg class="header-band" viewBox="0 0 950 260" preserveAspectRatio="none" aria-hidden="true">
      <path d="M0,0 H950 V248 C800,140 560,8 330,20 C200,26 80,40 0,60 Z" fill="var(--crimson)"/>
      <path d="M0,0 H950 V238 C800,132 560,2 330,15 C200,20 80,34 0,56 Z" fill="var(--paper)"/>
      <path d="M0,0 H950 V234 C800,128 560,-2 330,11 C200,16 80,32 0,55 Z" fill="var(--navy)"/>
    </svg>

    <address class="contact">
      <p>1475 Calloway Street, Suite 210</p>
      <p>Houston, Texas 77041</p>
      <p class="phone">Phone:832-361-9027</p>
      <p class="fax">Fax:832-614-7359</p>
    </address>

    <div class="brand">
      <div class="brand-square"></div>
      <div class="brand-name">Marwick Law</div>
    </div>

    <section class="letter-body">
      <p class="date">4th September 20XX</p>

      <div class="recipient">
        <p class="name">Ronny Reader</p>
        <p>CEO, Company Name</p>
        <p>123 Address St</p>
        <p>Anytown, ST 12345</p>
      </div>

      <div class="content">
        <p>Dear Mr. Reader,</p>
        <p>Lorem ipsum dolor sit amet, consectetuer adipiscing elit, sed diam nonummy nibh euismod tincidunt ut laoreet dolore magna aliquam erat volutpat. Ut wisi enim ad minim veniam, quis nostrud exerci tation ullamcorper suscipit lobortis nisl ut aliquip ex ea commodo consequat.</p>
        <p class="gap">Duis autem vel eum iriure dolor in hendrerit in vulputate velit esse molestie consequat, vel illum dolore eu feugiat nulla facilisis at vero eros et accumsan.</p>
        <p class="gap">Nam liber tempor cum soluta nobis eleifend option congue nihil imperdiet doming id quod mazim placerat facer possim assum. Typi non habent claritatem insitam; est usus legentis in iis qui facit eorum claritatem. Investigationes demonstraverunt lectores legere me lius quod ii legunt saepius.</p>
        <p>Sincerely,</p>
      </div>

      <div class="signature" role="img" aria-label="Handwritten signature"></div>
      <p class="signer">Your Name</p>
    </section>
  </main>
</body>
</html>
```